Velk Consulting -New consulting business in architecture, urban planning, and real estate development

We need a stationery design, including logo, business cards, etc, work for a new consulting business that works in the world of architectural, urban planning and real estate development.

The name of the company is "Velk Consulting". Velk is my last name but it of course also has the meaning 'cool' and 'hip'.

Target Market(s)

The business will provide boutique consulting services to high end clients that may include property developers, cities, etc.

Industry/Entity Type

Consultant

Contact Information for Business Card

VELK Consulting
First Name Last Name
Title
Phone number
Address
Website
Optional: Twitter handle

Logo Text

VELK Consulting

Font styles to use
Sans Serif

Colors

Designer to choose colors to be used in the design.

Requirements
Must have
• Simple design
• Easy to read font
• Modern
• Elegance
• Nice font that can be used for future reports, letters, etc.
• Good colour scheme that allows for the elegance to come through
Should not have
• Complex design ideas
• Complex logos
• Not a corporate feel and look

```html
<!DOCTYPE html>
<html lang="en">
<head>
<meta charset="utf-8">
<title>Velk Consulting – Envelopes</title>
<link rel="stylesheet" href="https://fonts.googleapis.com/css2?family=Montserrat:wght@400;500;700&display=swap">
<style>
  :root {
    --backdrop: #cbd9e0;
    --paper: #fbfbfb;
    --paper-shade: #eeeff1;
    --gold: #a58a2c;
    --gold-light: #c2a44c;
    --ink: #2a2a2a;
  }
  html, body {
    margin: 0;
    padding: 0;
    width: 1200px;
    height: 961px;
    overflow: hidden;
    background: var(--backdrop);
    font-family: "Montserrat", sans-serif;
  }
  .canvas {
    position: relative;
    width: 1200px;
    height: 961px;
  }
  .envelope-back {
    position: absolute;
    left: 68px;
    top: 308px;
    width: 484px;
    height: 328px;
  }
  .envelope-back svg { display: block; }
  .brand-name {
    font-family: "Montserrat", sans-serif;
    font-weight: 500;
    color: var(--gold);
    letter-spacing: 0.14em;
    text-transform: uppercase;
    white-space: nowrap;
  }
  .envelope-back .brand-name {
    position: absolute;
    left: 0;
    right: 0;
    top: 224px;
    text-align: center;
    font-size: 22px;
  }
  .envelope-front {
    position: absolute;
    left: 628px;
    top: 390px;
    width: 488px;
    height: 242px;
    background: var(--paper);
    box-shadow: 0 6px 14px rgba(60, 80, 95, 0.18);
  }
  .frame {
    position: absolute;
    left: 14px;
    top: 12px;
    right: 14px;
    bottom: 14px;
    border: 1px solid var(--gold-light);
  }
  .envelope-front .brand-name {
    position: absolute;
    left: 33px;
    top: 40px;
    font-size: 20px;
  }
  .return-address {
    position: absolute;
    left: 33px;
    top: 188px;
    font-size: 7px;
    color: var(--ink);
  }
  .return-address strong { font-weight: 700; }
  .contact-row {
    position: absolute;
    left: 33px;
    top: 202px;
    display: flex;
    align-items: center;
    font-size: 7px;
    color: var(--ink);
  }
  .contact-item {
    display: flex;
    align-items: center;
    gap: 4px;
    padding: 0 6px;
    border-left: 1px solid #bbb;
    line-height: 12px;
  }
  .contact-item:first-child { padding-left: 0; border-left: none; }
  .contact-item svg { width: 8px; height: 8px; }
</style>
</head>
<body>
<main class="canvas">

  <section class="envelope-back" aria-label="Envelope back with open flap">
    <svg width="484" height="328" viewBox="0 0 484 328">
      <defs>
        <linearGradient id="liner-tone" x1="0" y1="0" x2="0" y2="1">
          <stop offset="0" stop-color="#b8962f"/>
          <stop offset="1" stop-color="#c9a956"/>
        </linearGradient>
      </defs>
      <rect x="0" y="88" width="484" height="240" fill="var(--paper-shade)"/>
      <path d="M0 10 Q0 0 10 0 H474 Q484 0 484 10 V100 L450 134 H28 L0 100 Z"
            fill="url(#liner-tone)" role="img" aria-label="Gold ornamental mandala pattern liner"/>
      <polygon points="28,134 450,134 484,328 0,328" fill="var(--paper)"/>
      <line x1="0" y1="327.5" x2="484" y2="327.5" stroke="#d8dadd"/>
    </svg>
    <div class="brand-name">Velk Consulting</div>
  </section>

  <section class="envelope-front" aria-label="Envelope front">
    <div class="frame"></div>
    <div class="brand-name">Velk Consulting</div>
    <p class="return-address"><strong>Velk Consulting</strong> - 48 Harlow Avenue, Ridgeford, MS 39100</p>
    <div class="contact-row">
      <span class="contact-item">
        <svg viewBox="0 0 10 10" aria-hidden="true"><path d="M2 1 L4 1 L4.8 3 L3.6 4 Q4.6 6 6 6.6 L7 5.4 L9 6.2 L9 8 Q9 9 8 9 Q1 8.5 1 2 Q1 1 2 1 Z" fill="var(--gold)"/></svg>
        000 000 0000
      </span>
      <span class="contact-item">
        <svg viewBox="0 0 10 10" aria-hidden="true"><rect x="0.5" y="2" width="9" height="6" fill="none" stroke="var(--gold)"/><path d="M0.5 2 L5 5.5 L9.5 2" fill="none" stroke="var(--gold)"/></svg>
        info@velkconsulting.com
      </span>
      <span class="contact-item">
        <svg viewBox="0 0 10 10" aria-hidden="true"><circle cx="5" cy="5" r="4.3" fill="none" stroke="var(--gold)" stroke-width="0.8"/><ellipse cx="5" cy="5" rx="1.8" ry="4.3" fill="none" stroke="var(--gold)" stroke-width="0.8"/><line x1="0.7" y1="5" x2="9.3" y2="5" stroke="var(--gold)" stroke-width="0.8"/></svg>
        www.velkconsulting.com
      </span>
    </div>
  </section>

</main>
</body>
</html>
```